Calvanto Group Real Estate Company business cards

New business card design, we are generally happy with the basic layout of the existing front of business card, (feel free to change) but require a head shot photo on the back side.

http://www.calvanto.com.au/

Attached logos, and existing business card

------------------------------

Target Market(s)

Real estate

Industry/Entity Type

Real Estate

Contact Information for Business Card

Standard size double sided

Font styles to use
Other font styles liked:
• Futura

Requirements
Must have
• Photo head shot on the back side
Nice to have
• yes
Should not have
• No

```html
<!DOCTYPE html>
<html lang="en">
<head>
<meta charset="utf-8">
<title>Calvanto Group – Business Cards</title>
<link rel="stylesheet" href="https://fonts.googleapis.com/css2?family=Jost:wght@400;500;600;700&display=swap">
<style>
  :root {
    --purple: #2e1f63;
    --orange: #f6931f;
    --white: #ffffff;
    --ink: #3a3a3a;
    --muted: #8a8a96;
    --backdrop: #e6e6e9;
    --photo-light: #eef0f4;
    --photo-suit: #2a3b63;
  }
  * { box-sizing: border-box; margin: 0; padding: 0; }
  html, body {
    width: 1200px; height: 900px; overflow: hidden;
    background: var(--backdrop);
    font-family: "Jost", "Futura", sans-serif;
  }
  .canvas { position: relative; width: 1200px; height: 900px; }

  .card {
    position: absolute; width: 600px; height: 343px; overflow: hidden;
    box-shadow: 0 14px 30px rgba(0,0,0,.22);
  }

  /* ---------- Front card ---------- */
  .card-front { left: 130px; top: 100px; background: var(--white); }
  .card-front .headshot {
    position: absolute; right: 0; top: 24px; width: 230px; height: 214px;
    background: linear-gradient(180deg, var(--photo-light) 0%, var(--photo-light) 35%, var(--photo-suit) 36%, #1f2d4f 100%);
  }
  .card-front .brand { position: absolute; left: 52px; top: 120px; }
  .wordmark {
    font-weight: 500; font-size: 64px; line-height: 1; letter-spacing: 1px;
    color: var(--purple);
  }
  .brand-sub {
    display: block; text-align: right; font-size: 11px; letter-spacing: 6px;
    color: var(--muted); margin-top: 2px;
  }
  .card-front .site {
    position: absolute; left: 110px; top: 206px;
    font-size: 16px; line-height: 20px; color: var(--ink); letter-spacing: .5px;
  }
  .card-front .site b { color: var(--purple); font-weight: 700; }
  .card-front .rule-top {
    position: absolute; left: 0; right: 0; top: 238px; height: 3px; background: var(--orange);
  }
  .card-front .band {
    position: absolute; left: 0; right: 0; top: 244px; height: 60px; background: var(--purple);
  }
  .card-front .band-cover {
    position: absolute; left: 0; width: 330px; top: 241px; height: 36px; background: var(--white);
  }
  .card-front .services {
    position: absolute; left: 330px; top: 252px; width: 250px; text-align: center;
    color: var(--white); font-size: 20px; line-height: 28px; font-weight: 500; letter-spacing: 2px;
  }
  .card-front .rule-bottom {
    position: absolute; left: 0; right: 0; top: 310px; height: 3px; background: var(--orange);
  }

  /* ---------- Back card ---------- */
  .card-back { left: 470px; top: 480px; background: var(--purple); }
  .card-back .brand { position: absolute; left: 40px; top: 128px; }
  .card-back .wordmark { color: var(--white); font-size: 58px; }
  .card-back .brand-sub { color: #9a93bd; }
  .card-back .divider {
    position: absolute; left: 300px; top: 70px; width: 1px; height: 150px; background: #6b5fa0;
  }
  .contact { position: absolute; left: 318px; top: 66px; color: var(--white); }
  .contact .name { font-size: 27px; font-weight: 700; letter-spacing: 1px; line-height: 1; }
  .contact .role { color: var(--orange); font-size: 15px; font-weight: 500; margin-top: 2px; }
  .contact .abn { font-size: 14px; margin-top: 4px; }
  .contact .abn span { color: var(--orange); }
  .contact ul { list-style: none; margin-top: 6px; font-size: 14px; line-height: 1.5; }
  .contact li { display: flex; align-items: center; gap: 8px; }
  .contact svg { width: 12px; height: 12px; flex: none; }
  .card-back .strip-line { position: absolute; left: 0; right: 0; height: 2px; background: var(--white); }
  .card-back .strip-line.upper { top: 238px; }
  .card-back .strip-line.lower { top: 298px; }
  .card-back .tagline-band {
    position: absolute; left: 0; right: 0; top: 246px; height: 46px; background: var(--orange);
    display: flex; align-items: center; justify-content: flex-end; padding-right: 60px;
    color: var(--white); font-size: 24px; letter-spacing: .5px;
  }
</style>
</head>
<body>
<main class="canvas">

  <section class="card card-front" aria-label="Business card front">
    <div class="headshot" role="img" aria-label="Head shot photo of the director in a navy suit"></div>
    <div class="brand">
      <div class="wordmark">calvanto</div>
      <span class="brand-sub">GROUP</span>
    </div>
    <p class="site">www.<b>calvanto.com</b>.au</p>
    <div class="rule-top"></div>
    <div class="band"></div>
    <div class="band-cover"></div>
    <p class="services">Buy | Sell | Rent</p>
    <div class="rule-bottom"></div>
  </section>

  <section class="card card-back" aria-label="Business card back">
    <div class="brand">
      <div class="wordmark">calvanto</div>
      <span class="brand-sub">GROUP</span>
    </div>
    <div class="divider"></div>
    <div class="contact">
      <p class="name">DANIEL TRAN</p>
      <p class="role">DIRECTOR</p>
      <p class="abn"><span>ABN:</span> 51 824 630 197</p>
      <ul>
        <li>
          <svg viewBox="0 0 12 12" aria-hidden="true"><rect x="3" y="0.5" width="6" height="11" rx="1.2" fill="none" stroke="#f6931f" stroke-width="1.2"/><circle cx="6" cy="9.5" r=".7" fill="#f6931f"/></svg>
          0400 318 562
        </li>
        <li>
          <svg viewBox="0 0 12 12" aria-hidden="true"><rect x="0.6" y="2.5" width="10.8" height="7.5" fill="none" stroke="#f6931f" stroke-width="1.2"/><path d="M0.6 2.5 L6 7 L11.4 2.5" fill="none" stroke="#f6931f" stroke-width="1.2"/></svg>
          daniel.tran@calvanto.com.au
        </li>
        <li>
          <svg viewBox="0 0 12 12" aria-hidden="true"><circle cx="6" cy="6" r="5.2" fill="none" stroke="#f6931f" stroke-width="1.2"/><ellipse cx="6" cy="6" rx="2.2" ry="5.2" fill="none" stroke="#f6931f" stroke-width="1"/><path d="M1 6 H11" stroke="#f6931f" stroke-width="1"/></svg>
          www.calvanto.com.au
        </li>
      </ul>
    </div>
    <div class="strip-line upper"></div>
    <div class="tagline-band">your next home starts here</div>
    <div class="strip-line lower"></div>
  </section>

</main>
</body>
</html>
```